Landscape Construction and Design Company

We are a landscape construction and design company from New Jersey. We design and install landscapes and hardscapes for residential properties. The name of the company is Belwick's Landscape and Design LLC. We specialize mostly in planting trees and stone work, some water features. We would like to see design themes that include a tree or trees and a stone walkway or wall. We like earth tone colors. We like traditional to modern designs.

Target Market(s)

Homeowners

Industry/Entity Type

Landscape

Contact Information for Business Card

Nature themed design, earth tone colors, space for company name, address, phone numbers, email and website address

Logo Text

No text

Font styles to use
Serif

Colors

Designer to choose colors to be used in the design.

Requirements
Must have
• A tree or trees, similar to the ones uploaded in my supporting images
Nice to have
• I like trees similar to those in my uploaded supporting images. I like artistic, nature theme, earth tone colors
Should not have
• Pictures of real landscapes, cartoon looking logo or objects

```html
<!DOCTYPE html>
<html lang="en">
<head>
<meta charset="utf-8">
<title>Belwick's Landscape and Design LLC — Business Card</title>
<link rel="stylesheet" href="https://fonts.googleapis.com/css2?family=Amatic+SC:wght@700&family=Caveat:wght@500&family=Cabin:wght@600&display=swap">
<style>
  :root {
    --page-bg: #e6eaea;
    --card-bg: #f1f3cb;
    --card-bg-deep: #e7eab8;
    --forest: #2f3d36;
    --forest-soft: #3a4b42;
    --leaf: #1f5a3a;
    --bark: #6a4518;
    --shadow: rgba(40, 50, 45, 0.22);
  }
  html, body {
    margin: 0;
    padding: 0;
    width: 1200px;
    height: 1015px;
    overflow: hidden;
    background: var(--page-bg);
  }
  .canvas {
    position: relative;
    width: 1200px;
    height: 1015px;
  }
  .business-card {
    position: absolute;
    left: 120px;
    top: 215px;
    width: 960px;
    height: 585px;
    background: linear-gradient(180deg, var(--card-bg) 0%, var(--card-bg-deep) 100%);
    box-shadow: 0 14px 30px var(--shadow);
    overflow: hidden;
  }
  .tree-band {
    position: absolute;
    left: 0;
    width: 100%;
    display: block;
  }
  .tree-band--top { top: 0; height: 125px; }
  .tree-band--bottom { bottom: 0; height: 118px; }
  .brand {
    position: absolute;
    left: 0;
    right: 0;
    top: 128px;
    text-align: center;
  }
  .brand__name {
    margin: 0;
    font-family: "Amatic SC", "Georgia", serif;
    font-weight: 700;
    font-size: 160px;
    line-height: 1;
    letter-spacing: 2px;
    color: var(--forest);
  }
  .brand__tagline {
    margin: 0;
    font-family: "Caveat", cursive;
    font-weight: 500;
    font-size: 36px;
    line-height: 1;
    letter-spacing: 2px;
    color: var(--leaf);
  }
  .contact {
    position: absolute;
    left: 0;
    right: 0;
    top: 380px;
    text-align: center;
    font-family: "Cabin", sans-serif;
    font-weight: 600;
    font-size: 22px;
    color: var(--bark);
  }
  .contact__row {
    margin: 0 0 8px;
    line-height: 28px;
  }
  .contact__item + .contact__item {
    border-left: 2px solid var(--forest);
    padding-left: 8px;
    margin-left: 6px;
  }
</style>
</head>
<body>
<main class="canvas">
  <section class="business-card">
    <svg class="tree-band tree-band--top" viewBox="0 0 960 125" preserveAspectRatio="none" role="img" aria-label="Row of hanging tree silhouettes along the top edge">
      <rect x="0" y="0" width="960" height="16" fill="var(--forest)"/>
      <path d="M0 16 H960 V95 Q900 125 840 100 Q780 80 720 95 Q660 110 600 92 Q540 78 480 96 Q420 112 360 94 Q300 78 240 96 Q180 112 120 94 Q60 78 0 96 Z" fill="var(--forest-soft)" opacity="0.9"/>
    </svg>

    <header class="brand">
      <h1 class="brand__name">Belwick's</h1>
      <p class="brand__tagline">landscape and design llc.</p>
    </header>

    <address class="contact">
      <p class="contact__row"><span class="contact__item">your adress adress</span><span class="contact__item">your phone number</span><span class="contact__item">your celphone number</span></p>
      <p class="contact__row"><span class="contact__item">your e-mail adress</span><span class="contact__item">your website adress</span></p>
    </address>

    <svg class="tree-band tree-band--bottom" viewBox="0 0 960 118" preserveAspectRatio="none" role="img" aria-label="Row of tree silhouettes along the bottom edge">
      <path d="M0 40 Q60 10 120 36 Q180 12 240 38 Q300 10 360 36 Q420 12 480 38 Q540 10 600 36 Q660 12 720 38 Q780 10 840 36 Q900 12 960 38 V100 H0 Z" fill="var(--forest-soft)" opacity="0.9"/>
      <path d="M0 100 Q240 92 480 102 Q720 110 960 98 V118 H0 Z" fill="var(--forest)"/>
    </svg>
  </section>
</main>
</body>
</html>
```